Professional Website for Leading Global Private Equity Real Estate Company

The company is a leading global Private Equity Real Estate (PERE). We need a homepage design, an inner page design, and color/font tweaks to the logo (color should be more soothing than current blue used in the logo). The logo website should project the company as global, professional, experienced, trustworthy, accessible, YOUNG, DYNAMIC, hi-tech. PLEASE SEE the attached Design Brief Word Doc for details.

Target Market(s)

institional investors and wealthy private individuals

Industry/Entity Type

Finance

Number of Pages Required

2 page

Font styles to use
Sans Serif
Other font styles liked:
• either like in https://www.ferndalequay.com/ or like in presentations (Montserrat Black & Montserrat Light, Century Gothic, Blair ITC, Almoni Neue DL 4.0 AAA Medium, Almoni DL AAA)

Requirements
Must have
• new color palette that is NOT based on current logo. they want a more soothing color palette than the blue in that logo. the new color palette should project: global, professional, experienced, trustworthy, accessible, YOUNG, DYNAMIC, hi-tech.
Nice to have
• the likes these sites: https://www.ferndalequay.com/ and https://www.tvr.law/

```html
<!DOCTYPE html>
<html lang="en">
<head>
<meta charset="utf-8">
<title>Halvane Real Estate</title>
<link href="https://fonts.googleapis.com/css2?family=Montserrat:wght@400;500;600;700&family=Open+Sans:wght@400;600&display=swap" rel="stylesheet">
<style>
:root{
  --sky:#4cc6f7;
  --sky-soft:#a9e3fb;
  --navy:#1b2f48;
  --navy-deep:#0f1c2e;
  --gold:#b8893a;
  --gold-light:#e6c77a;
  --grey:#eff0f2;
  --ink:#111;
  --text:#333;
  --white:#fff;
}
*{margin:0;padding:0;box-sizing:border-box}
html,body{width:1200px;height:4380px;overflow:hidden}
body{position:relative;background:var(--white);font-family:"Open Sans",Arial,sans-serif;color:var(--text)}
.abs{position:absolute}
h1,h2,h3,h4,.brand,.nav a,.btn{font-family:"Montserrat",Arial,sans-serif}
.btn{position:absolute;background:var(--sky);color:var(--white);border-radius:30px;font-size:15px;font-weight:600;display:flex;align-items:center;justify-content:center}
.brand{position:absolute;display:flex;align-items:center;gap:10px;font-size:22px;font-weight:500;letter-spacing:2px;color:var(--white)}
.brand .dot{width:26px;height:26px;border-radius:50%;background:var(--sky)}
/* hero */
.hero-svg{position:absolute;left:0;top:0}
.nav{position:absolute;left:508px;top:34px;display:flex;gap:30px;font-size:14.5px;color:var(--white)}
.nav a{color:var(--white);text-decoration:none}
.nav a.active{color:var(--sky)}
.hero-title{position:absolute;left:110px;top:172px;font-size:42px;line-height:50px;font-weight:600;color:var(--white)}
.hero-rule{position:absolute;left:110px;top:296px;width:388px;height:2px;background:var(--white)}
.hero-sub{position:absolute;left:112px;top:310px;font-size:17px;line-height:26px;font-weight:600;color:var(--white);font-family:"Montserrat",sans-serif}
/* about */
.kicker{position:absolute;left:0;width:1200px;text-align:center;color:var(--sky);font-size:19px;font-family:"Montserrat",sans-serif}
.section-title{position:absolute;left:0;width:1200px;text-align:center;font-size:34px;font-weight:500;color:var(--ink)}
.lead{position:absolute;left:176px;width:848px;text-align:center;font-size:14.5px;line-height:25.7px;color:var(--text)}
.counter{position:absolute;top:991px;width:184px;height:184px;border-radius:50%;background:var(--sky);border:6px solid var(--sky-soft);color:var(--white);text-align:center;font-family:"Montserrat",sans-serif}
.counter b{display:block;font-size:66px;font-weight:500;line-height:70px;margin-top:28px}
.counter span{font-size:22px}
/* platforms */
.platforms{position:absolute;left:0;top:1248px;width:1200px;height:472px;background:var(--grey)}
.card{position:absolute;top:1366px;width:182px}
.card .ph{width:182px;height:168px;border:4px solid var(--white);box-shadow:0 1px 4px rgba(0,0,0,.15)}
.card h3{font-size:21px;font-weight:600;color:var(--ink);margin:14px 0 0 6px}
.card p{font-size:14px;line-height:22px;margin:6px 0 0 6px;color:var(--text)}
.card a{display:block;margin:6px 0 0 6px;font-size:13px;color:var(--sky);font-weight:600;font-family:"Montserrat",sans-serif}
/* feature */
.feature-title{position:absolute;font-size:34px;font-weight:500;color:var(--ink)}
.feature-text{position:absolute;width:478px;font-size:14.5px;line-height:25.8px;color:var(--text)}
/* newsletter band */
.band{position:absolute;left:0;top:2319px;width:1200px;height:309px;background:linear-gradient(90deg,#3fb3e8,#57ccf8 50%,#44b8ea)}
.band h2{position:absolute;left:0;top:42px;width:1200px;text-align:center;color:var(--white);font-size:35px;font-weight:500}
.band p{position:absolute;left:270px;top:106px;width:660px;text-align:center;color:var(--white);font-size:14.5px;line-height:25px}
.band .field{position:absolute;left:284px;top:192px;width:493px;height:58px;border:2px solid var(--white);border-radius:30px;color:var(--white);font-size:16px;padding:17px 34px}
.band .sub{position:absolute;left:792px;top:192px;width:160px;height:58px;border-radius:30px;background:var(--white);color:var(--sky);font-family:"Montserrat",sans-serif;font-weight:600;font-size:17px;display:flex;align-items:center;justify-content:center}
/* contact */
.contact{position:absolute;left:0;top:3222px;width:1200px;height:800px;background:var(--grey)}
.info{position:absolute;left:172px;display:flex;gap:14px}
.info .ic{width:56px;height:56px;border-radius:50%;background:var(--white);box-shadow:0 2px 8px rgba(0,0,0,.08);display:flex;align-items:center;justify-content:center;flex:none}
.info h4{font-size:16px;font-weight:600;color:var(--ink);margin-top:2px}
.info p{font-size:14.5px;line-height:23px;margin-top:3px;color:var(--text)}
.form{position:absolute;left:583px;top:3361px;width:440px;height:442px;background:var(--white)}
.form h3{position:absolute;left:47px;top:38px;font-size:21px;font-weight:600;color:var(--ink)}
.form .row{position:absolute;left:48px;width:346px;border-bottom:1.5px solid #333;font-size:15px;color:#222;padding-bottom:10px}
.form .row.select::after{content:"";position:absolute;right:4px;top:7px;border:5px solid transparent;border-top:6px solid #222}
/* footer */
.footer-col h4{position:absolute;font-size:21px;font-weight:600;color:var(--white)}
.links{position:absolute;list-style:none;font-size:14.5px;line-height:30px;color:var(--white)}
.foot-text{position:absolute;left:112px;top:4131px;width:260px;font-size:14.5px;line-height:30px;color:var(--white)}
.foot-field{position:absolute;left:835px;top:4112px;width:258px;height:34px;border:1px solid #555;font-size:13px;color:#777;padding:8px 10px}
.social{position:absolute;top:4180px;width:14px;height:14px;border-radius:50%;background:var(--white)}
.copy{position:absolute;left:0;top:4327px;width:1200px;text-align:center;font-size:14.5px;color:var(--white)}
</style>
</head>
<body>

<!-- hero -->
<svg class="hero-svg" width="1200" height="700" viewBox="0 0 1200 700">
  <defs>
    <linearGradient id="heroShade" x1="0" y1="0" x2="1" y2="1">
      <stop offset="0" stop-color="#1a3656"/>
      <stop offset=".55" stop-color="#2a4663"/>
      <stop offset="1" stop-color="#4a3a2e"/>
    </linearGradient>
  </defs>
  <polygon points="0,570 298,683 1200,548 1200,560 298,686" fill="var(--sky)"/>
  <polygon role="img" aria-label="Photo of business team meeting around a boardroom table" points="0,0 1200,0 1200,548 298,670 0,570" fill="url(#heroShade)"/>
  <path d="M470 328h20m-8-8 8 8-8 8" stroke="#fff" stroke-width="2.5" fill="none"/>
</svg>
<div class="brand" style="left:110px;top:28px"><span class="dot"></span>HALVANE REAL ESTATE</div>
<nav class="nav"><a class="active">Home</a><a>About Us</a><a>Our Businesses</a><a>investors Lobby</a><a>News</a><a>Contact Us</a></nav>
<h1 class="hero-title">Welcome To<br>Halvane Real Estate</h1>
<div class="hero-rule"></div>
<p class="hero-sub">Lorem ipsum dolor sit amet,<br>consectetur adipiscing elit, sed</p>
<div class="btn" style="left:114px;top:384px;width:150px;height:53px">About Us</div>

<!-- about -->
<p class="kicker" style="top:746px">About Us</p>
<h2 class="section-title" style="top:770px">Halvane Real Estate</h2>
<p class="lead" style="top:826px">Lorem ipsum dolor sit amet, consectetur adipiscing elit, sed do eiusmod tempor incididunt ut labore et dolore magna aliqua. Quis ipsum suspendisse ultrices gravida. Risus commodo viverra maecenas accumsan lacus vel facilisis. Lorem ipsum dolor sit amet, consectetur adipiscing elit, sed do eiusmod tempor incididunt ut labore et dolore magna aliqua. Quis ipsum suspendisse ultrices gravida. Risus commodo viverra maecenas accumsan lacus vel facilisis. Lorem ipsum dolor sit amet, consectetur adipiscing elit, sed do eiusmod tempor incididunt ut labore et</p>
<div class="counter" style="left:154px"><b>38</b><span>Days</span></div>
<div class="counter" style="left:391px"><b>912</b><span>Hours</span></div>
<div class="counter" style="left:627px"><b>10</b><span>Mins</span></div>
<div class="counter" style="left:863px"><b>05</b><span>seconds</span></div>

<!-- platforms -->
<section class="platforms"></section>
<h2 class="section-title" style="top:1296px">Our Investment Platforms</h2>
<div class="card" style="left:110px"><div class="ph" role="img" aria-label="Photo of hands sheltering stacked coins" style="background:linear-gradient(135deg,#2e4a66,#8a7a68)"></div><h3>Lorem Ipsum</h3><p>Lorem ipsum dolor sit amet, consectetur</p><a>Learn More &rarr;</a></div>
<div class="card" style="left:311px"><div class="ph" role="img" aria-label="Photo of a digital property model on a desk" style="background:linear-gradient(135deg,#3a4b5c,#9a7b5a)"></div><h3>Lorem Ipsum</h3><p>Lorem ipsum dolor sit amet, consectetur</p><a>Learn More &rarr;</a></div>
<div class="card" style="left:510px"><div class="ph" role="img" aria-label="Photo of a contract being signed" style="background:linear-gradient(135deg,#3b3f46,#a9a39b)"></div><h3>Lorem Ipsum</h3><p>Lorem ipsum dolor sit amet, consectetur</p><a>Learn More &rarr;</a></div>
<div class="card" style="left:707px"><div class="ph" role="img" aria-label="Photo of colleagues reviewing a tablet" style="background:linear-gradient(135deg,#c9ced3,#7c6b60)"></div><h3>Lorem Ipsum</h3><p>Lorem ipsum dolor sit amet, consectetur</p><a>Learn More &rarr;</a></div>
<div class="card" style="left:904px"><div class="ph" role="img" aria-label="Photo of a small wooden house model" style="background:linear-gradient(135deg,#5a4a3e,#c7b59e)"></div><h3>Lorem Ipsum</h3><p>Lorem ipsum dolor sit amet, consectetur</p><a>Learn More &rarr;</a></div>

<!-- our edge -->
<svg class="abs" style="left:100px;top:1790px" width="470" height="460" viewBox="0 0 470 460">
  <defs><linearGradient id="gold1" x1="0" y1="0" x2="1" y2="1"><stop offset="0" stop-color="var(--gold)"/><stop offset=".5" stop-color="var(--gold-light)"/><stop offset="1" stop-color="var(--gold)"/></linearGradient></defs>
  <circle cx="233" cy="231" r="222" fill="url(#gold1)"/>
  <circle role="img" aria-label="Photo of two businessmen discussing work at a laptop" cx="233" cy="231" r="208" fill="#2a3340"/>
</svg>
<h2 class="feature-title" style="left:615px;top:1826px">Our Edge</h2>
<p class="feature-text" style="left:617px;top:1882px">Lorem ipsum dolor sit amet, consectetur adipiscing elit, sed do eiusmod tempor incididunt ut labore et dolore magna aliqua. Quis ipsum suspendisse ultrices gravida. Risus commodo viverra maecenas accumsan lacus vel facilisis. Lorem ipsum dolor sit amet, consectetur adipiscing elit, sed do eiusmod tempor incididunt ut labore et dolore magna aliqua. Quis ipsum suspendisse ultrices gravida. Risus commodo viverra maecenas accumsan lacus vel facilisis. Lorem ipsum dolor sit amet, consectetur adipiscing elit, sed do eiusmod tempor incididunt ut labore et dolore magna aliqua. Lorem ipsum dolor sit amet, consectetur adipiscing elit, sed</p>
<div class="btn" style="left:619px;top:2157px;width:151px;height:53px">Learn More</div>

<!-- stay updated -->
<section class="band" role="img" aria-label="Blue tinted band over a faint office backdrop">
  <h2>Stay Updated</h2>
  <p>Lorem ipsum dolor sit amet, consectetur adipiscing elit, sed do eiusmod tempor incididunt ut labore et dolore magna aliqua. Quis ipsum suspendisse ultrices gravida.</p>
  <div class="field">Enter Your Email</div>
  <div class="sub">Subscribe</div>
</section>

<!-- our responsibility -->
<h2 class="feature-title" style="left:112px;top:2726px">Our Responsibility</h2>
<p class="feature-text" style="left:115px;top:2783px">Lorem ipsum dolor sit amet, consectetur adipiscing elit, sed do eiusmod tempor incididunt ut labore et dolore magna aliqua. Quis ipsum suspendisse ultrices gravida. Risus commodo viverra maecenas accumsan lacus vel facilisis. Lorem ipsum dolor sit amet, consectetur adipiscing elit, sed do eiusmod tempor incididunt ut labore et dolore magna aliqua. Quis ipsum suspendisse ultrices gravida. Risus commodo viverra maecenas accumsan lacus vel facilisis. Lorem ipsum dolor sit amet, consectetur adipiscing elit, sed do eiusmod tempor incididunt ut labore et dolore magna aliqua. Lorem ipsum dolor sit amet, consectetur adipiscing elit, sed</p>
<div class="btn" style="left:116px;top:3057px;width:151px;height:54px">Learn More</div>
<svg class="abs" style="left:640px;top:2690px" width="470" height="460" viewBox="0 0 470 460">
  <defs><linearGradient id="gold2" x1="0" y1="0" x2="1" y2="1"><stop offset="0" stop-color="var(--gold)"/><stop offset=".5" stop-color="var(--gold-light)"/><stop offset="1" stop-color="var(--gold)"/></linearGradient></defs>
  <circle cx="232" cy="231" r="222" fill="url(#gold2)"/>
  <circle role="img" aria-label="Photo of coin stacks and a calculator on financial papers" cx="232" cy="231" r="208" fill="#6e747c"/>
</svg>

<!-- contact -->
<section class="contact"></section>
<h2 class="section-title" style="top:3278px">Contact Us</h2>
<div class="info" style="top:3446px"><div class="ic"><svg width="18" height="18" viewBox="0 0 24 24"><path d="M12 2a7 7 0 0 0-7 7c0 5 7 13 7 13s7-8 7-13a7 7 0 0 0-7-7zm0 9.5A2.5 2.5 0 1 1 12 6.5a2.5 2.5 0 0 1 0 5z" fill="var(--sky)"/></svg></div><div><h4>Address</h4><p>Lorem ipsum dolor sit amet, consectetur<br>adipiscing elit</p></div></div>
<div class="info" style="top:3558px"><div class="ic"><svg width="18" height="18" viewBox="0 0 24 24"><path d="M6.6 10.8a15 15 0 0 0 6.6 6.6l2.2-2.2a1 1 0 0 1 1-.25 11.4 11.4 0 0 0 3.6.57 1 1 0 0 1 1 1V20a1 1 0 0 1-1 1A17 17 0 0 1 3 4a1 1 0 0 1 1-1h3.5a1 1 0 0 1 1 1c0 1.250.2 2.450.57 3.6a1 1 0 0 1-.25 1z" fill="var(--sky)"/></svg></div><div><h4>Phone</h4><p>+1 555 010 0188</p></div></div>
<div class="info" style="top:3660px"><div class="ic"><svg width="18" height="18" viewBox="0 0 24 24"><path d="M3 5h18v14H3z" fill="var(--sky)"/><path d="M3 5l9 7 9-7" stroke="#fff" stroke-width="1.6" fill="none"/></svg></div><div><h4>Email</h4><p style="color:var(--sky)">info@halvanerealestate.com</p></div></div>
<div class="form">
  <h3>Send Message</h3>
  <div class="row" style="top:96px">Full Name</div>
  <div class="row select" style="top:154px">Last Name</div>
  <div class="row" style="top:217px">Address</div>
  <div class="row" style="top:281px">Types Your Message</div>
  <div class="btn" style="left:49px;top:353px;width:109px;height:41px">Send</div>
</div>

<!-- footer -->
<svg class="abs" style="left:0;top:3880px" width="1200" height="500" viewBox="0 0 1200 500">
  <polygon points="0,150 898,13 1200,107 1200,500 0,500" fill="#000"/>
  <polygon points="0,140 898,13 1200,107 1200,112 898,24 0,150" fill="var(--sky)"/>
  <line x1="110" y1="421" x2="1093" y2="421" stroke="#333" stroke-width="1"/>
</svg>
<div class="brand" style="left:110px;top:4072px;font-size:17px;gap:8px"><span class="dot" style="width:20px;height:20px"></span>HALVANE REAL ESTATE</div>
<p class="foot-text">Lorem ipsum dolor sit amet, consectetur adipiscing elit, sed do eiusmod tempor incididunt</p>
<div class="footer-col"><h4 style="left:411px;top:4059px">Quick Link</h4></div>
<ul class="links" style="left:417px;top:4101px"><li>Home</li><li>About Us</li><li>Our Businesses</li><li>investors Lobby</li><li>News</li><li>Contact Us</li></ul>
<div class="footer-col"><h4 style="left:629px;top:4059px">Help Link</h4></div>
<ul class="links" style="left:634px;top:4101px"><li>Terms&amp;condtions</li><li>Privacy Policy</li><li>About Us</li><li>Support</li></ul>
<div class="footer-col"><h4 style="left:833px;top:4059px">Get Our Newsletter</h4></div>
<div class="foot-field">Enter Your Email</div>
<svg class="abs" style="left:1066px;top:4120px" width="18" height="18" viewBox="0 0 24 24"><path d="M2 12 22 3l-5 18-5-7z" fill="var(--sky)"/></svg>
<span class="social" style="left:842px"></span>
<span class="social" style="left:866px"></span>
<span class="social" style="left:890px"></span>
<span class="social" style="left:914px"></span>
<p class="copy">©Copyrights 2022 Halvane Real Estate | &nbsp; All Rights Reserved</p>

</body>
</html>
```